Medical Billing Company Needs a Business Card Design

We need a business card design for a Florida based medical billing company called 'Clinicians Keystone Solutions'. We specialize in providing revenue cycle management services to physician and therapist offices (we're basically their back-office processing partner for providing billing software, claims submissions, A/R follow-up and patient statements & collections. Our logo is red and blue-ish, so make sure that whatever other elements are used will match appropriately. Our current business card design has a too small font size. I'd like to project an image that shows we are modern & reliable. On a side note, I'm planning on using ZUB for printing these cards.

Target Market(s)

Office managers, physicians, therapists

Industry/Entity Type

Printing

Requirements
Must have
• Logo
Name of Employee
Phone
Fax
E-mail
Website

```html
<!DOCTYPE html>
<html lang="en">
<head>
<meta charset="utf-8">
<title>Clinicians Keystone Solutions – Business Card</title>
<link href="https://fonts.googleapis.com/css2?family=Open+Sans:wght@400;600;700&display=swap" rel="stylesheet">
<style>
  :root {
    --backdrop: #ecebe8;
    --paper: #ffffff;
    --navy-violet: #3a2a86;
    --deep-violet: #2b1a74;
    --brand-red: #b0202a;
    --red-dark: #86080f;
    --red-light: #b9353c;
    --ink: #2f2f2f;
    --rule: #c9c9c9;
  }
  * { margin: 0; padding: 0; box-sizing: border-box; }
  html, body { width: 1200px; height: 720px; overflow: hidden; }
  body {
    background: var(--backdrop);
    font-family: "Open Sans", Arial, sans-serif;
    display: flex;
    align-items: center;
    justify-content: center;
    gap: 40px;
  }
  .card {
    position: relative;
    width: 540px;
    height: 309px;
    overflow: hidden;
    box-shadow: 0 6px 18px rgba(0,0,0,0.18);
  }
  /* Front */
  .card--front { background: var(--paper); }
  .front-band { position: absolute; left: 0; bottom: 0; width: 540px; height: 309px; }
  .brand-name {
    position: absolute;
    left: 36px; top: 128px;
    font-size: 19px;
    font-weight: 600;
    letter-spacing: 1.2px;
    color: var(--navy-violet);
    text-transform: uppercase;
  }
  .divider {
    position: absolute;
    left: 318px; top: 30px;
    width: 1px; height: 140px;
    background: var(--rule);
  }
  .contact { position: absolute; left: 334px; top: 30px; }
  .person-name { font-size: 19px; font-weight: 700; color: var(--navy-violet); line-height: 1.1; }
  .person-title { font-size: 12px; color: var(--brand-red); margin-bottom: 10px; }
  .contact-line {
    display: flex; align-items: center; gap: 7px;
    font-size: 12.5px; color: var(--ink); line-height: 20px;
  }
  .contact-line svg { width: 11px; height: 11px; flex: none; }
  .address {
    position: absolute; left: 30px; bottom: 26px;
    font-size: 13px; color: var(--ink);
  }
  .front-web {
    position: absolute; right: 22px; bottom: 52px;
    font-size: 13px; font-weight: 600; color: #fff; letter-spacing: 0.3px;
  }
  /* Back */
  .card--back {
    background: radial-gradient(ellipse at 50% 35%, var(--red-light) 0%, var(--brand-red) 40%, var(--red-dark) 100%);
    color: #fff;
    display: flex; flex-direction: column; align-items: center; justify-content: center;
  }
  .back-brand {
    display: flex; align-items: center; gap: 12px;
    font-size: 24px; font-weight: 600; letter-spacing: 1.5px; text-transform: uppercase;
    margin-bottom: 70px;
  }
  .back-brand .mark-square { width: 18px; height: 18px; border: 2px solid #fff; }
  .back-web {
    position: absolute; bottom: 40px; left: 0; right: 0; text-align: center;
    font-size: 15px; letter-spacing: 4px;
  }
</style>
</head>
<body>

  <section class="card card--front" aria-label="Business card front">
    <svg class="front-band" viewBox="0 0 540 309" aria-hidden="true">
      <rect x="0" y="283" width="540" height="3" fill="var(--brand-red)"/>
      <path d="M0 288 H300 C318 288 318 258 340 258 H540 V309 H0 Z" fill="var(--deep-violet)"/>
      <path d="M0 292 H300 C318 292 318 262 340 262 H540" fill="none" stroke="#6a5cb0" stroke-width="1"/>
    </svg>

    <div class="brand-name">Clinicians Keystone</div>
    <div class="divider"></div>

    <div class="contact">
      <div class="person-name">Your Name</div>
      <div class="person-title">Title</div>
      <div class="contact-line">
        <svg viewBox="0 0 12 12"><circle cx="6" cy="6" r="5.5" fill="none" stroke="var(--ink)"/><path d="M4 3.5 L5 3.5 L5.5 5 L4.8 5.6 Q5.6 7 6.5 7.3 L7.1 6.6 L8.5 7.1 L8.5 8.2 Q5 8.6 3.6 4.6 Z" fill="var(--ink)"/></svg>
        123-456-0789
      </div>
      <div class="contact-line">
        <svg viewBox="0 0 12 12"><rect x="3.5" y="1" width="5" height="10" rx="1" fill="var(--ink)"/><rect x="4.5" y="2.5" width="3" height="5" fill="#fff"/></svg>
        123-456-0789
      </div>
      <div class="contact-line">
        <svg viewBox="0 0 12 12"><circle cx="6" cy="6" r="6" fill="var(--ink)"/><rect x="3" y="4" width="6" height="4.2" fill="#fff"/><path d="M3 4 L6 6.4 L9 4" fill="none" stroke="var(--ink)" stroke-width="0.8"/></svg>
        info@cliniciankeystone.com
      </div>
    </div>

    <div class="front-web">www.cliniciankeystone.com</div>
    <div class="address">Street Name, City Name, State Zip Code</div>
  </section>

  <section class="card card--back" aria-label="Business card back">
    <div class="back-brand"><span class="mark-square"></span>Clinicians Keystone</div>
    <div class="back-web">www.cliniciankeystone.com</div>
  </section>

</body>
</html>
```